Snoutsaver.net Dog Coupon Site Website Design

TailThrift - Dog Coupon Site Design Brief

Project Overview
**Site Name:** SnoutSaver.net
**Purpose:** A modern coupon aggregation platform specifically for dog and pet-related products and services
**Target Audience:** Dog owners, pet enthusiasts, budget-conscious pet parents

Brand Identity & Visual Direction

Typography
- **Headers:** Modern sans-serif (Inter or similar) - Clean and friendly
- **Body:** Readable sans-serif with good mobile legibility
- **Accent:** Playful but professional font for coupon codes

Design Principles
- **Flat Design:** Clean, minimal with subtle shadows
- **Friendly & Approachable:** Rounded corners, soft edges
- **Trust-Building:** Clear pricing, transparent savings
- **Scannable:** Easy-to-read coupon codes and offers

## User Experience & Functionality

### Homepage Features
1. **Hero Section**
- Clear value proposition
- Search functionality
- Featured savings highlight

2. **Coupon Cards**
- One-click copy functionality
- Clear discount display
- Store/brand logos
- Expiration dates
- "Get Deal" call-to-action

3. **Navigation**
- Categories (Food, Toys, Health, Services, etc.)
- Popular stores
- Latest deals

### Interactive Elements
- **Copy Button:** Instant feedback when coupon copied
- **Deal Pages:** Detailed offer information, terms, store details
- **Search & Filter:** By category, store, discount amount
- **Mobile Menu:** Hamburger navigation for mobile

## Technical Requirements

### Responsive Design
- **Mobile-First:** Optimized for touch interactions
- **Tablet:** Adapted layout for medium screens
- **Desktop:** Full-width utilization with sidebar potential

### Performance
- **Fast Loading:** Optimized images, minimal JavaScript
- **Accessibility:** WCAG compliant, screen reader friendly
- **SEO Optimized:** Structured data for deals and offers

## Content Strategy

### Deal Categories
- Dog Food & Treats
- Toys & Accessories
- Health & Grooming
- Training & Services
- Outdoor & Travel

### Key Messaging
- "Save on everything your dog loves"
- "Verified deals updated daily"
- "Your pup deserves the best for less"

## Conversion Optimization

### Trust Elements
- Deal verification badges
- User reviews/ratings
- Clear savings calculations
- Expiration date transparency

### Call-to-Actions
- "Copy Code" (primary action)
- "Get Deal" (secondary action)
- "View All [Store] Deals"

## Success Metrics
- Coupon copy rate
- Click-through to retailer
- User return visits
- Mobile vs desktop usage
- Category performance

This design brief ensures a user-friendly, trustworthy platform that makes finding and using pet deals effortless while maintaining a warm, dog-loving community feel.

1. Design Objective
Create a warm, energetic space where dog lovers instantly feel welcomed and confident they’re finding genuine savings for their furry friends. Everything from the layout to the smallest icon should reinforce trust, delight, and simplicity.
2. Visual Personality
Color Palette: Soft, cheerful hues—think warm yellows and gentle blues—that evoke sunshine and playfulness without overwhelming.
Typography:
Headings: A modern, friendly sans‑serif (like Inter) with open letterforms to feel approachable.
Body Copy: Highly legible sans‑serif with generous line spacing for comfort on small screens.
Accent Font: A slightly quirky, hand‑drawn style used sparingly for coupon codes and special call‑outs, giving a personal, “paw‑picked” touch.
Imagery & Icons: Real‑life photographs of happy dogs interspersed with clean line‑icons of bones, paw prints, and hearts. Rounded shapes and subtle shadows keep the look soft and contemporary.
3. Layout & Hierarchy
Hero Area:
Full‑bleed image of a joyful dog, overlaid with a single, punchy tagline (“Save on everything your dog loves”).
Prominent search bar centered to invite exploration.
Offer Grid:
Generous white space around each coupon card so the eye can rest and scan easily.
Coupon cards feature a bold discount label, brand logo, and a friendly “Get Deal” button.
A playful “Copied!” animation briefly replaces the button once the code is grabbed.
Navigation:
A fixed header with clear category labels (Food, Toys, Health, Services).
A secondary “Popular Stores” carousel below to spotlight key partners.
4. Interaction & Motion
Micro‑interactions:
Hover state for cards subtly lifts the card and deepens its shadow, inviting a click.
Copy‑code button pulses once on hover, hinting at its one‑click magic.
Transitions:
Smooth fades between deal filters and search results to reassure users that the site is responding.
Loading indicators shaped like spinning collars or wagging tails to keep the theme consistent.
5. Accessibility & Inclusivity
Ensure all text meets contrast standards so every pet parent—regardless of vision—can read offers with ease.
Interactive elements sized for easy tapping on touchscreens.
Alt‑text for all imagery describing dogs, products, and actions for screen‑reader users.
6. Emotional Tone
From the moment someone lands on SnoutSaver.net, they should feel the joy of treating their dog without guilt. Friendly copy (“Your pup deserves the best for less”) paired with bright visuals will create a sense of community and shared passion.
7. Success by Design
Scan‑ability: Users should spot great deals in under two seconds.
Trust Signals: Badges (“Verified Savings”), clear expiration dates, and reviewer star icons should feel earned and prominent.
Return Visits: A “My Favorite Deals” heart icon encourages saving and returning, reinforced by subtle reminders in the UI.
This design approach keeps dog lovers front and center—making sure every graphic, font choice, and interaction feels like it was lovingly tailored for them.

Target Market(s)

Dog Lovers looking for good deals

Industry/Entity Type

Coupon Code

Number of Pages Required

4 page

Font styles to use
Sans Serif

Requirements
Must have
• Modern look, coupon copy cards it's a deal site and I want the coupon code and copy in the coupon card, blog section, review section, modern footer/header
Nice to have
• Modern coupon code website, easy to use

```html
<!DOCTYPE html>
<html lang="en">
<head>
<meta charset="utf-8">
<title>SnoutSaver – Save on everything your dog loves</title>
<link href="https://fonts.googleapis.com/css2?family=Inter:wght@400;500;600;700;800&family=Poppins:wght@500;600;700&display=swap" rel="stylesheet">
<style>
:root{
  --orange:#f47b20;
  --orange-soft:#fff1e6;
  --teal:#1d5f5c;
  --ink:#161616;
  --muted:#6b6b6b;
  --line:#e6e6e6;
  --band:#f3f3f3;
  --footer:#121212;
  --white:#ffffff;
  --star:#f5a623;
}
*{box-sizing:border-box;margin:0;padding:0}
html,body{width:1200px;height:4712px;overflow:hidden}
body{font-family:Inter,Arial,sans-serif;color:var(--ink);background:var(--white);position:relative}
.abs{position:absolute}
/* hero */
.hero{position:absolute;left:0;top:0;width:1200px;height:600px;overflow:hidden}
.hero-photo{position:absolute;inset:0;background:linear-gradient(180deg,#7d8f4a 0%,#5f8a2c 40%,#4f8a1f 70%,#3e6f17 100%)}
.hero-dog{position:absolute;left:830px;top:120px;width:300px;height:440px;border-radius:45% 45% 30% 30%;background:radial-gradient(circle at 50% 40%,#f4efe6,#d9d0c1 70%,rgba(217,208,193,0) 72%)}
.nav{position:absolute;top:0;left:0;width:1200px;height:80px;display:flex;align-items:center;padding:0 140px}
.brand{font-family:Poppins,Arial,sans-serif;font-weight:600;font-size:26px;color:var(--white)}
.nav ul{list-style:none;display:flex;gap:34px;margin-left:auto}
.nav li{color:var(--white);font-size:15px;font-weight:500}
.nav li.active{border-bottom:2px solid var(--white);padding-bottom:4px}
.hero h1{position:absolute;left:150px;top:170px;font-size:68px;line-height:1.12;font-weight:700;color:var(--white);letter-spacing:-1px}
.search{position:absolute;left:150px;top:430px;width:600px;height:58px;background:var(--white);border-radius:30px;display:flex;align-items:center;padding:0 8px 0 24px;font-size:15px;color:var(--muted)}
.search .cat{width:170px;border-right:1px solid var(--line);display:flex;justify-content:space-between;align-items:center;padding-right:16px;color:var(--ink)}
.search .field{flex:1;padding-left:18px}
.search .go{width:44px;height:44px;border-radius:50%;background:var(--orange);display:flex;align-items:center;justify-content:center}
/* section titles */
.sec-title{position:absolute;left:0;width:1200px;text-align:center;font-size:40px;font-weight:700}
.sec-title::after{content:"";display:block;width:40px;height:3px;background:var(--ink);margin:16px auto 0}
.deco{position:absolute;border-radius:50%}
/* coupon cards */
.grid{position:absolute;left:152px;display:grid;grid-template-columns:repeat(4,212px);gap:16px}
.card{background:var(--white);border-radius:14px;box-shadow:0 4px 18px rgba(0,0,0,.10);overflow:hidden;position:relative;height:488px;padding:0 14px}
.card .photo{margin:0 -14px;height:160px;position:relative}
.badge{position:absolute;left:10px;top:10px;background:var(--orange);color:var(--white);font-size:11px;font-weight:700;padding:5px 9px;border-radius:4px}
.chip{position:absolute;left:12px;bottom:-12px;background:var(--white);border:1px solid var(--teal);color:var(--teal);font-size:11px;padding:3px 10px;border-radius:12px}
.store{font-family:Poppins,Arial,sans-serif;font-weight:700;font-size:22px;color:var(--orange);margin-top:28px;height:40px;display:flex;align-items:center;gap:8px}
.store i{width:10px;height:10px;background:var(--orange);display:inline-block;border-radius:50%}
.card h3{font-size:16px;font-weight:600;line-height:1.35;margin-top:6px}
.price{font-size:18px;font-weight:700;margin-top:10px}
.price s{font-size:13px;color:var(--muted);font-weight:400;margin-left:6px}
.exp{font-size:12px;color:var(--muted);margin-top:8px}
.copy{position:absolute;left:14px;right:14px;bottom:62px;height:36px;border:1px dashed var(--teal);background:#e8f1f0;color:var(--teal);border-radius:8px;font-size:12px;font-weight:600;display:flex;align-items:center;justify-content:center;font-family:Poppins,Arial,sans-serif}
.copy.done{background:var(--teal);color:var(--white);border-style:solid}
.deal{position:absolute;left:14px;right:14px;bottom:18px;height:36px;background:var(--orange);color:var(--white);border-radius:8px;font-size:13px;font-weight:600;display:flex;align-items:center;justify-content:center}
.btn-outline{position:absolute;height:44px;border:1.5px solid var(--orange);border-radius:22px;color:var(--orange);font-size:15px;font-weight:600;display:flex;align-items:center;justify-content:center;background:var(--white)}
/* categories */
.band{position:absolute;left:0;width:1200px;background:var(--band)}
.cats{position:absolute;left:152px;top:2252px;display:grid;grid-template-columns:repeat(3,288px);gap:16px}
.cat-card{height:300px;border-radius:14px;position:relative;overflow:hidden}
.cat-card span{position:absolute;left:22px;bottom:20px;color:var(--white);font-size:24px;font-weight:600}
.cat-card svg{position:absolute;right:22px;bottom:26px}
.dots{position:absolute;left:0;width:1200px;display:flex;justify-content:center;gap:10px}
.dots i{width:10px;height:10px;border-radius:50%;background:#c7c7c7;display:block}
.dots i.on{background:var(--ink)}
.arrow{position:absolute;width:44px;height:44px;border-radius:50%;border:1.5px solid #9a9a9a;background:var(--white);display:flex;align-items:center;justify-content:center}
.off{display:inline-block;background:var(--ink);color:var(--white);font-size:10px;padding:3px 6px;border-radius:8px;margin-right:6px;vertical-align:middle}
.pct{font-size:18px;font-weight:700}
/* stores */
.stores{position:absolute;left:152px;top:3528px;display:grid;grid-template-columns:repeat(5,164px);gap:20px 19px}
.logo-box{height:88px;background:var(--white);border-radius:12px;box-shadow:0 3px 12px rgba(0,0,0,.08);display:flex;align-items:center;justify-content:center;gap:8px;font-weight:700;font-size:16px;color:var(--ink)}
.logo-box i{width:22px;height:22px;background:var(--ink);border-radius:50%;display:block}
/* reviews */
.rev-title{position:absolute;left:150px;top:3930px;font-size:40px;font-weight:700}
.rev-title::after{content:"";display:block;width:40px;height:3px;background:var(--ink);margin-top:14px}
.score{position:absolute;left:800px;top:3930px;display:flex;align-items:center;gap:12px}
.score .ring{width:56px;height:56px;border-radius:50%;background:var(--teal);color:var(--white);font-weight:700;font-size:18px;display:flex;align-items:center;justify-content:center}
.score p{font-size:14px;color:var(--muted)}
.score b{color:var(--ink)}
.reviews{position:absolute;left:152px;top:4032px;display:grid;grid-template-columns:repeat(3,288px);gap:16px}
.review{height:290px;border:1px solid var(--line);border-radius:14px;background:var(--white);padding:24px 26px;position:relative}
.quote{font-size:56px;line-height:.8;color:var(--teal);font-weight:800;font-family:Poppins,Arial,sans-serif}
.stars{color:var(--star);font-size:20px;letter-spacing:2px;margin-top:4px}
.review p{font-size:13px;line-height:1.6;color:var(--muted);margin-top:10px}
.who{position:absolute;left:26px;bottom:24px;display:flex;align-items:center;gap:12px;font-size:13px}
.who i{width:40px;height:40px;border-radius:50%;background:#c9b8a3;display:block}
.who small{display:block;color:var(--muted);font-size:11px}
/* footer */
.footer{position:absolute;left:0;top:4412px;width:1200px;height:300px;background:var(--footer);color:var(--white)}
.footer .brand{position:absolute;left:150px;top:46px;font-size:30px}
.fcol{position:absolute;top:44px}
.fcol h4{font-size:13px;font-weight:700;letter-spacing:.5px;margin-bottom:14px}
.fcol li{list-style:none;font-size:12px;color:#bdbdbd;margin-bottom:9px}
.socials{display:flex;gap:8px}
.socials i{width:28px;height:28px;border-radius:50%;background:var(--white);display:block}
.verified{margin-top:18px;display:inline-flex;align-items:center;gap:8px;border:1px solid #444;border-radius:20px;padding:7px 14px;font-size:12px}
.copyright{position:absolute;left:0;bottom:22px;width:1200px;text-align:center;font-size:12px;color:#9a9a9a;border-top:1px solid #2a2a2a;padding-top:20px}
</style>
</head>
<body>

<header class="hero">
  <div class="hero-photo" role="img" aria-label="Happy small white dog running across a sunny green lawn"></div>
  <div class="hero-dog" role="img" aria-label="Fluffy white dog bounding toward the camera"></div>
  <nav class="nav">
    <div class="brand">SnoutSaver</div>
    <ul><li class="active">Categories</li><li>Popular stores</li><li>Latest deals</li><li>Contact Us</li></ul>
  </nav>
  <h1>Save on everything<br>your dog loves</h1>
  <div class="search">
    <div class="cat">Categories <svg width="10" height="6"><path d="M0 0h10L5 6z" fill="#161616"/></svg></div>
    <div class="field">Search</div>
    <div class="go"><svg width="18" height="18" viewBox="0 0 18 18"><circle cx="7.5" cy="7.5" r="5.5" fill="none" stroke="#fff" stroke-width="2"/><path d="M12 12l4 4" stroke="#fff" stroke-width="2" stroke-linecap="round"/></svg></div>
  </div>
</header>

<div class="abs" style="left:0;top:690px;width:120px;height:70px;border-radius:30px;background:linear-gradient(135deg,#f1dfc0,#d9c29a);transform:rotate(-25deg)" role="img" aria-label="Dog bone treat"></div>
<div class="deco" style="left:1130px;top:650px;width:90px;height:90px;background:radial-gradient(circle,#9a5a2a,#5a3516)" role="img" aria-label="Bowl of dog kibble"></div>
<div class="deco" style="left:1140px;top:1210px;width:70px;height:70px;background:radial-gradient(circle,#e84a3c,#2c6fd1)" role="img" aria-label="Colourful rope toy"></div>
<div class="deco" style="left:-20px;top:1720px;width:50px;height:50px;background:radial-gradient(circle,#d63a2f,#7a1c14)" role="img" aria-label="Red ball toy"></div>

<h2 class="sec-title" style="top:705px">Our Coupon</h2>

<div class="grid" style="top:852px">
  <article class="card"><div class="photo" style="background:linear-gradient(135deg,#a7683a,#5a3a22)" role="img" aria-label="Bowl of dry dog food"><span class="badge">20% OFF</span><span class="chip">Food</span></div>
    <div class="store"><i></i>WagWell</div><h3>Lorem Ipsum is simply dummy text</h3><div class="price">$15.00<s>$35.00</s></div><div class="exp">Expiry Date : 25 June, 2025</div>
    <div class="copy">Copy Code : 25dell23</div><div class="deal">Get Deal</div></article>
  <article class="card"><div class="photo" style="background:linear-gradient(135deg,#7fa85a,#c9a36a)" role="img" aria-label="Puppy playing on grass"><span class="badge">30% OFF</span><span class="chip">Toys</span></div>
    <div class="store"><i></i>Tailo</div><h3>Lorem Ipsum is simply dummy text</h3><div class="price">$65.00<s>$120.00</s></div><div class="exp">Expiry Date : 25 June, 2025</div>
    <div class="copy done">Copied Code!</div><div class="deal">Get Deal</div></article>
  <article class="card"><div class="photo" style="background:linear-gradient(135deg,#5b7fb8,#c89a62)" role="img" aria-label="Dog being groomed"><span class="badge">40% OFF</span><span class="chip">Grooming</span></div>
    <div class="store"><i></i>Nuvio</div><h3>Lorem Ipsum is simply dummy text</h3><div class="price">$22.00<s>$45.00</s></div><div class="exp">Expiry Date : 25 June, 2025</div>
    <div class="copy">Copy Code : 25dell23</div><div class="deal">Get Deal</div></article>
  <article class="card"><div class="photo" style="background:linear-gradient(135deg,#6e9a3e,#d9c24a)" role="img" aria-label="Dog carrying a tennis ball"><span class="badge">15% OFF</span><span class="chip">Outdoor</span></div>
    <div class="store"><i></i>Regal Hound</div><h3>Lorem Ipsum is simply dummy text</h3><div class="price">$35.00<s>$55.00</s></div><div class="exp">Expiry Date : 25 June, 2025</div>
    <div class="copy">Copy Code : 25dell23</div><div class="deal">Get Deal</div></article>

  <article class="card"><div class="photo" style="background:linear-gradient(135deg,#e8e2da,#9a6a3e)" role="img" aria-label="Bowl of kibble on white"><span class="badge">20% OFF</span><span class="chip">Food</span></div>
    <div class="store"><i></i>WagWell</div><h3>Lorem Ipsum is simply dummy text</h3><div class="price">$15.00<s>$35.00</s></div><div class="exp">Expiry Date : 25 June, 2025</div>
    <div class="copy">Copy Code : 25dell23</div><div class="deal">Get Deal</div></article>
  <article class="card"><div class="photo" style="background:linear-gradient(135deg,#f08aa8,#52b8c0)" role="img" aria-label="Colourful chew toys"><span class="badge">30% OFF</span><span class="chip">Toys</span></div>
    <div class="store"><i></i>Tailo</div><h3>Lorem Ipsum is simply dummy text</h3><div class="price">$65.00<s>$120.00</s></div><div class="exp">Expiry Date : 25 June, 2025</div>
    <div class="copy">Copy Code : 25dell23</div><div class="deal">Get Deal</div></article>
  <article class="card"><div class="photo" style="background:linear-gradient(135deg,#8a8e96,#d8c6a8)" role="img" aria-label="Dog at grooming table"><span class="badge">40% OFF</span><span class="chip">Grooming</span></div>
    <div class="store"><i></i>Nuvio</div><h3>Lorem Ipsum is simply dummy text</h3><div class="price">$22.00<s>$45.00</s></div><div class="exp">Expiry Date : 25 June, 2025</div>
    <div class="copy">Copy Code : 25dell23</div><div class="deal">Get Deal</div></article>
  <article class="card"><div class="photo" style="background:linear-gradient(135deg,#9bbf5a,#c8a26e)" role="img" aria-label="Dog outdoors on a lawn"><span class="badge">15% OFF</span><span class="chip">Outdoor</span></div>
    <div class="store"><i></i>Regal Hound</div><h3>Lorem Ipsum is simply dummy text</h3><div class="price">$35.00<s>$55.00</s></div><div class="exp">Expiry Date : 25 June, 2025</div>
    <div class="copy">Copy Code : 25dell23</div><div class="deal">Get Deal</div></article>
</div>

<div class="btn-outline" style="left:520px;top:1960px;width:160px">View All Deals</div>

<div class="band" style="top:2100px;height:560px" role="img" aria-label="Light grey background with soft paw print pattern"></div>
<div class="abs" style="left:30px;top:1930px;width:300px;height:180px;border-radius:40% 50% 10% 10%;background:linear-gradient(135deg,#7a4522,#3a2010)" role="img" aria-label="Dachshund lying down"></div>
<div class="abs" style="left:840px;top:1900px;width:260px;height:210px;border-radius:45% 45% 10% 10%;background:linear-gradient(135deg,#e2a866,#b36b2e)" role="img" aria-label="Orange cat peeking over the edge"></div>

<h2 class="sec-title" style="top:2135px">Categories</h2>
<div class="cats">
  <div class="cat-card" style="background:linear-gradient(135deg,#8a5a34,#2e2a26)" role="img" aria-label="Bowls of dog food and treats"><span>Food</span><svg width="28" height="16" viewBox="0 0 28 16"><path d="M0 8h25M18 1l7 7-7 7" fill="none" stroke="#fff" stroke-width="2"/></svg></div>
  <div class="cat-card" style="background:linear-gradient(135deg,#3f6f9a,#a5b7c6)" role="img" aria-label="Blue plush bone toys"><span>Toys</span><svg width="28" height="16" viewBox="0 0 28 16"><path d="M0 8h25M18 1l7 7-7 7" fill="none" stroke="#fff" stroke-width="2"/></svg></div>
  <div class="cat-card" style="background:linear-gradient(135deg,#d9d3cc,#c23a4a)" role="img" aria-label="Dog and cat beside a first aid kit"><span>Health</span><svg width="28" height="16" viewBox="0 0 28 16"><path d="M0 8h25M18 1l7 7-7 7" fill="none" stroke="#fff" stroke-width="2"/></svg></div>
</div>
<div class="dots" style="top:2595px"><i class="on"></i><i></i><i></i><i></i></div>

<h2 class="sec-title" style="top:2705px">Latest Deals</h2>
<div class="arrow" style="left:56px;top:2940px"><svg width="14" height="14" viewBox="0 0 14 14"><path d="M9 2L4 7l5 5" fill="none" stroke="#555" stroke-width="2"/></svg></div>
<div class="arrow" style="left:1100px;top:2940px"><svg width="14" height="14" viewBox="0 0 14 14"><path d="M5 2l5 5-5 5" fill="none" stroke="#555" stroke-width="2"/></svg></div>
<div class="grid" style="top:2812px">
  <article class="card" style="height:476px"><div class="photo" style="background:linear-gradient(135deg,#b23a3a,#6a8a3a)" role="img" aria-label="Heart shaped bowl of wet food"><span class="chip">Food</span></div>
    <div class="store"><i></i>WagWell</div><h3>Lorem Ipsum is simply dummy text</h3><div class="price"><span class="off">UPTO</span><span class="pct">25% OFF</span></div><div class="exp">Expiry Date : 2 days Ago</div>
    <div class="copy done">Copied</div><div class="deal">Get Deal</div></article>
  <article class="card" style="height:476px"><div class="photo" style="background:linear-gradient(135deg,#d7b58a,#8a6a4a)" role="img" aria-label="Puppy with toys"><span class="chip">Toys &amp; Accessories</span></div>
    <div class="store"><i></i>WagWell</div><h3>Lorem Ipsum is simply dummy text</h3><div class="price"><span class="off">UPTO</span><span class="pct">35% OFF</span></div><div class="exp">Expiry Date : 2 days Ago</div>
    <div class="copy">Copy Code</div><div class="deal">Get Deal</div></article>
  <article class="card" style="height:476px"><div class="photo" style="background:linear-gradient(135deg,#e6ddd0,#a88a6a)" role="img" aria-label="Dog being brushed"><span class="chip">Health &amp; Grooming</span></div>
    <div class="store"><i></i>WagWell</div><h3>Lorem Ipsum is simply dummy text</h3><div class="price"><span class="off">UPTO</span><span class="pct">75% OFF</span></div><div class="exp">Expiry Date : 2 days Ago</div>
    <div class="copy">Copy Code</div><div class="deal">Get Deal</div></article>
  <article class="card" style="height:476px"><div class="photo" style="background:linear-gradient(135deg,#3a4a6a,#b0a090)" role="img" aria-label="Dog with travel backpack"><span class="chip">Outdoor &amp; Travel</span></div>
    <div class="store"><i></i>WagWell</div><h3>Lorem Ipsum is simply dummy text</h3><div class="price"><span class="off">UPTO</span><span class="pct">50% OFF</span></div><div class="exp">Expiry Date : 2 days Ago</div>
    <div class="copy">Copy Code</div><div class="deal">Get Deal</div></article>
</div>

<div class="band" style="top:3380px;height:500px;background:linear-gradient(180deg,#f7f7f7,#ececec)" role="img" aria-label="Soft light grey studio backdrop"></div>
<div class="abs" style="left:0;top:3730px;width:170px;height:150px;border-radius:50% 50% 10% 10%;background:linear-gradient(135deg,#c98a4a,#e0452f)" role="img" aria-label="Dog holding a red ball"></div>
<h2 class="sec-title" style="top:3410px">Popular Stores</h2>
<div class="arrow" style="left:56px;top:3612px"><svg width="14" height="14" viewBox="0 0 14 14"><path d="M9 2L4 7l5 5" fill="none" stroke="#555" stroke-width="2"/></svg></div>
<div class="arrow" style="left:1100px;top:3612px"><svg width="14" height="14" viewBox="0 0 14 14"><path d="M5 2l5 5-5 5" fill="none" stroke="#555" stroke-width="2"/></svg></div>
<div class="stores">
  <div class="logo-box"><i></i>Cozy Coat</div><div class="logo-box"><i></i>Lark Dog</div><div class="logo-box"><i></i>Watch Paw</div><div class="logo-box"><i></i>Merry Mutt</div><div class="logo-box"><i></i>Furlane</div>
  <div class="logo-box"><i></i>Cozy Coat</div><div class="logo-box"><i></i>Lark Dog</div><div class="logo-box"><i></i>Watch Paw</div><div class="logo-box"><i></i>Merry Mutt</div><div class="logo-box"><i></i>Furlane</div>
</div>
<div class="btn-outline" style="left:518px;top:3780px;width:164px">View All Stores</div>

<h2 class="rev-title">Reviews</h2>
<div class="score"><div class="ring">4.9</div><div><div class="stars" style="font-size:16px">★★★★★</div><p><b>4.9</b> Ratings from <b>254</b> Reviews</p></div></div>
<div class="reviews">
  <div class="review"><div class="quote">“</div><div class="stars">★★★★★</div><p>Great savings on food and treats every month. Codes worked first time and the expiry dates were clear, so I never missed a deal for my pup.</p><div class="who"><i></i><div><b>Dana Reyes</b><small>2 days Ago</small></div></div></div>
  <div class="review"><div class="quote">“</div><div class="stars">★★★★★</div><p>Great savings on food and treats every month. Codes worked first time and the expiry dates were clear, so I never missed a deal for my pup.</p><div class="who"><i></i><div><b>Dana Reyes</b><small>2 days Ago</small></div></div></div>
  <div class="review"><div class="quote">“</div><div class="stars">★★★★★</div><p>Great savings on food and treats every month. Codes worked first time and the expiry dates were clear, so I never missed a deal for my pup.</p><div class="who"><i></i><div><b>Dana Reyes</b><small>2 days Ago</small></div></div></div>
</div>
<div class="abs" style="left:1000px;top:4230px;width:200px;height:190px;border-radius:50% 50% 8% 8%;background:linear-gradient(135deg,#d89a4a,#8a5a2a)" role="img" aria-label="Golden puppy lying with toys"></div>
<div class="dots" style="top:4360px"><i class="on"></i><i></i><i></i><i></i><i></i><i></i></div>

<footer class="footer">
  <div class="brand">SnoutSaver</div>
  <div class="fcol" style="left:400px"><h4>MENU</h4><ul><li>Categories</li><li>Popular stores</li><li>Latest deals</li><li>Contact Us</li></ul></div>
  <div class="fcol" style="left:545px"><h4>CATEGORIES</h4><ul><li>Dog Food &amp; Treats</li><li>Toys &amp; Accessories</li><li>Health &amp; Grooming</li><li>Training &amp; Services</li><li>Outdoor &amp; Travel</li></ul></div>
  <div class="fcol" style="left:725px"><h4>LINKS</h4><ul><li>Terms &amp; Conditions</li><li>FAQ</li><li>Blog</li><li>Privacy</li></ul></div>
  <div class="fcol" style="left:880px"><h4>FOLLOW US</h4><div class="socials"><i></i><i></i><i></i><i></i><i></i></div>
    <div class="verified"><svg width="18" height="18" viewBox="0 0 18 18"><circle cx="9" cy="9" r="9" fill="#f47b20"/><path d="M5 9.5l2.5 2.5L13 6.5" fill="none" stroke="#fff" stroke-width="2"/></svg>100% Deal Verified</div></div>
  <div class="copyright">Copyright © 2025 All Rights Reserved</div>
</footer>

</body>
</html>
```